Birch Hauling Business Card Design Project

We need a new company business card. We provide professional timber harvesting (logging) and forest management services. I'm open to any creative design. Most company caps and shirts are navy blue and Light grey. Logo does not necessarily have to contain those colors. Logo containing picture of logging equipment, log truck, trees, or logs are acceptable. Be creative. Final logo should communicate our company's pride and professionalism in the East Texas Timber Industry.
Updates

Target Market(s)

Timber owners, sawmills, and forestry professionals

Industry/Entity Type

Business

Requirements
Must have
• Must have Contact Info.
Phone: 936-402-5917
address: PO Box 4830
New Waverly, Tx 77358
www.jmbirchhauling.example
jmbirchhauling@mailbox.example
Owner: Jared Marsh

Or design must leave room for this info.

```html
<!DOCTYPE html>
<html lang="en">
<head>
<meta charset="utf-8">
<title>Birch Hauling – Business Card</title>
<link rel="stylesheet" href="https://fonts.googleapis.com/css2?family=Exo+2:wght@400;500;600;700&display=swap">
<style>
  :root {
    --backdrop: #e4e4e2;
    --card-white: #f7f7f7;
    --card-shade: #e9e9e9;
    --brand-red: #e3262b;
    --brand-red-deep: #c81d22;
    --charcoal: #3a3a3c;
    --ink: #2b2b2b;
  }
  * { margin: 0; padding: 0; box-sizing: border-box; }
  html, body {
    width: 1200px; height: 900px; overflow: hidden;
    background: var(--backdrop);
    font-family: "Exo 2", Arial, sans-serif;
    color: var(--ink);
  }
  .canvas {
    width: 1200px; height: 900px;
    display: flex; align-items: center; justify-content: center;
  }
  .business-card {
    position: relative;
    width: 1050px; height: 600px;
    border-radius: 60px;
    overflow: hidden;
    background: radial-gradient(ellipse at 45% 35%, var(--card-white) 0%, var(--card-shade) 100%);
    box-shadow: 0 14px 40px rgba(0,0,0,0.18);
  }
  .card-waves { position: absolute; inset: 0; width: 100%; height: 100%; }
  .contact-list {
    position: absolute; left: 62px; top: 178px;
    list-style: none;
  }
  .contact-item {
    display: flex; align-items: center; gap: 18px;
    height: 38px;
    font-size: 22px; font-weight: 500; letter-spacing: 1px;
  }
  .contact-icon { width: 22px; height: 22px; fill: var(--ink); flex: none; }
  .brand-lockup {
    position: absolute; left: 600px; top: 150px;
    display: flex; align-items: center; gap: 18px;
  }
  .brand-mark {
    width: 30px; height: 30px; background: var(--brand-red); flex: none;
  }
  .brand-name {
    font-size: 40px; font-weight: 700; line-height: 1.05;
    color: var(--ink); text-transform: uppercase; letter-spacing: 1px;
  }
  .holder {
    position: absolute; left: 610px; top: 300px;
    text-align: center; width: 330px;
    text-transform: uppercase;
  }
  .holder-name { font-size: 36px; font-weight: 500; letter-spacing: 2px; }
  .holder-role { font-size: 21px; font-weight: 500; letter-spacing: 2px; margin-top: 4px; }
</style>
</head>
<body>
<main class="canvas">
  <section class="business-card" aria-label="Birch Hauling business card">
    <svg class="card-waves" viewBox="0 0 1050 600" preserveAspectRatio="none" aria-hidden="true">
      <path fill="var(--charcoal)" d="M0,372 C300,445 620,490 1050,372 L1050,452 C620,548 270,478 0,392 Z"/>
      <path fill="var(--brand-red)" d="M0,408 C260,488 600,568 1050,478 L1050,600 L0,600 Z"/>
      <path fill="var(--brand-red)" d="M560,462 C790,440 940,400 1050,325 L1050,352 C950,410 790,452 560,462 Z"/>
    </svg>

    <ul class="contact-list">
      <li class="contact-item">
        <svg class="contact-icon" viewBox="0 0 24 24"><path d="M6.6 10.8a15.1 15.1 0 0 0 6.6 6.6l2.2-2.2a1 1 0 0 1 1-.25 11.4 11.4 0 0 0 3.6.57 1 1 0 0 1 1 1V20a1 1 0 0 1-1 1A17 17 0 0 1 3 4a1 1 0 0 1 1-1h3.5a1 1 0 0 1 1 1c0 1.25.2 2.45.57 3.57a1 1 0 0 1-.25 1z"/></svg>
        <span>012 345 6789</span>
      </li>
      <li class="contact-item">
        <svg class="contact-icon" viewBox="0 0 24 24"><path d="M7 1h10a2 2 0 0 1 2 2v18a2 2 0 0 1-2 2H7a2 2 0 0 1-2-2V3a2 2 0 0 1 2-2zm0 3v14h10V4zm5 15.5a1 1 0 1 0 0 2 1 1 0 0 0 0-2z"/></svg>
        <span>012 345 6789</span>
      </li>
      <li class="contact-item">
        <svg class="contact-icon" viewBox="0 0 24 24"><path d="M7 2h10v5H7zM4 8h16a2 2 0 0 1 2 2v8h-4v4H6v-4H2v-8a2 2 0 0 1 2-2zm4 8v4h8v-4z"/></svg>
        <span>012 345 6789</span>
      </li>
      <li class="contact-item">
        <svg class="contact-icon" viewBox="0 0 24 24"><path d="M2 5h20v14H2zm2 2v.5l8 5 8-5V7zm0 2.8V17h16V9.8l-8 5z"/></svg>
        <span>urname@mailbox.example</span>
      </li>
      <li class="contact-item">
        <svg class="contact-icon" viewBox="0 0 24 24"><path d="M12 2a10 10 0 1 0 0 20 10 10 0 0 0 0-20zm6.9 6h-3a15 15 0 0 0-1.3-3.9A8 8 0 0 1 18.9 8zM12 4c.8 1.1 1.5 2.5 1.9 4h-3.8c.4-1.5 1.1-2.9 1.9-4zM4.3 14a8 8 0 0 1 0-4h3.4a16 16 0 0 0 0 4zm.8 2h3a15 15 0 0 0 1.3 3.9A8 8 0 0 1 5.1 16zm3-8h-3a8 8 0 0 1 4.3-3.9A15 15 0 0 0 8.1 8zM12 20c-.8-1.1-1.5-2.5-1.9-4h3.8c-.4 1.5-1.1 2.9-1.9 4zm2.3-6H9.7a14 14 0 0 1 0-4h4.6a14 14 0 0 1 0 4zm.3 5.9a15 15 0 0 0 1.3-3.9h3a8 8 0 0 1-4.3 3.9zM16.3 14a16 16 0 0 0 0-4h3.4a8 8 0 0 1 0 4z"/></svg>
        <span>www.urwebsitename.example</span>
      </li>
    </ul>

    <div class="brand-lockup">
      <span class="brand-mark" aria-hidden="true"></span>
      <p class="brand-name">Jared Marsh<br>Birch Hauling</p>
    </div>

    <div class="holder">
      <p class="holder-name">Daniel Reeve</p>
      <p class="holder-role">Financial Advisor</p>
    </div>
  </section>
</main>
</body>
</html>
```